Velk Consulting -New consulting business in architecture, urban planning, and real estate development

We need a stationery design, including logo, business cards, etc, work for a new consulting business that works in the world of architectural, urban planning and real estate development.

The name of the company is "Velk Consulting". Velk is my last name but it of course also has the meaning 'cool' and 'hip'.

Target Market(s)

The business will provide boutique consulting services to high end clients that may include property developers, cities, etc.

Industry/Entity Type

Consultant

Contact Information for Business Card

VELK Consulting
First Name Last Name
Title
Phone number
Address
Website
Optional: Twitter handle

Logo Text

VELK Consulting

Font styles to use
Sans Serif

Colors

Designer to choose colors to be used in the design.

Requirements
Must have
• Simple design
• Easy to read font
• Modern
• Elegance
• Nice font that can be used for future reports, letters, etc.
• Good colour scheme that allows for the elegance to come through
Should not have
• Complex design ideas
• Complex logos
• Not a corporate feel and look

```html
<!DOCTYPE html>
<html lang="en">
<head>
<meta charset="utf-8">
<title>VELK Consulting — Stationery</title>
<link rel="stylesheet" href="https://fonts.googleapis.com/css2?family=Montserrat:wght@400;500;600&display=swap">
<style>
  :root {
    --bg: #1f1f1f;
    --paper-dark: #141414;
    --paper-dark-2: #181818;
    --paper-light: #f4f4f2;
    --ink: #2b2b2b;
    --ink-soft: #6b6b6b;
    --white: #f2f2f2;
    --line: #d9d9d9;
    --gold: #b08a2e;
  }
  * { box-sizing: border-box; margin: 0; padding: 0; }
  html, body { width: 1200px; height: 957px; overflow: hidden; background: var(--bg); }
  body { font-family: "Montserrat", sans-serif; position: relative; }
  .piece { position: absolute; }

  .wordmark { font-weight: 600; line-height: 1; }
  .wordmark .name { display: block; letter-spacing: 0.04em; }
  .wordmark .sub { display: block; letter-spacing: 0.32em; margin-top: 0.15em; }

  /* Backing sheet */
  .backing { left: 98px; top: 188px; width: 344px; height: 538px; background: var(--paper-dark); }
  .backing::after { content: ""; position: absolute; inset: 0 8px 8px 0; border: 2px solid var(--line); }

  /* Letterhead */
  .letterhead { left: 48px; top: 110px; width: 390px; height: 552px; background: var(--paper-light); color: var(--ink); box-shadow: 0 6px 18px rgba(0,0,0,.35); }
  .letterhead .wordmark { position: absolute; left: 29px; top: 32px; color: var(--ink); }
  .letterhead .wordmark .name { font-size: 36px; }
  .letterhead .wordmark .sub { font-size: 7.5px; }
  .recipient { position: absolute; left: 37px; top: 152px; font-size: 7px; line-height: 1.35; color: var(--ink); }
  .recipient strong { font-weight: 600; }
  .recipient span { color: var(--ink-soft); }
  .date { position: absolute; right: 36px; top: 181px; font-size: 7px; color: var(--ink-soft); }
  .body-text { position: absolute; left: 37px; right: 37px; top: 219px; font-size: 5.4px; line-height: 2.15; color: var(--ink-soft); text-align: justify; }
  .body-text p { text-indent: 8px; margin-bottom: 8px; }
  .letter-footer { position: absolute; left: 37px; right: 30px; top: 524px; display: flex; gap: 6px; font-size: 5.3px; color: var(--ink); align-items: center; }
  .letter-footer .sep { width: 1px; height: 10px; background: #bbb; }
  .letter-footer svg { width: 7px; height: 7px; vertical-align: -1px; margin-right: 2px; }

  /* Envelope back */
  .envelope-back { left: 520px; top: 104px; width: 386px; height: 203px; background: var(--paper-dark-2); }
  .envelope-back svg.flap { position: absolute; inset: 0; }
  .envelope-back .wordmark { position: absolute; left: 163px; top: 22px; color: var(--white); }
  .envelope-back .wordmark .name { font-size: 22px; }
  .envelope-back .wordmark .sub { font-size: 4.5px; }

  /* Envelope front */
  .envelope-front { left: 606px; top: 330px; width: 388px; height: 193px; background: var(--paper-dark-2); color: var(--white); }
  .envelope-front::after { content: ""; position: absolute; left: 26px; top: 13px; right: 13px; bottom: 14px; border: 1.5px solid var(--line); }
  .envelope-front .wordmark { position: absolute; left: 36px; top: 39px; }
  .envelope-front .wordmark .name { font-size: 26px; }
  .envelope-front .wordmark .sub { font-size: 5.5px; }
  .envelope-front .contact { position: absolute; left: 36px; top: 121px; font-size: 5px; line-height: 1.5; }
  .envelope-front .return { position: absolute; left: 36px; top: 144px; font-size: 5px; line-height: 1.5; }
  .envelope-front strong { font-weight: 600; }

  /* Notebook */
  .notebook { left: 664px; top: 564px; width: 184px; height: 368px; background: var(--paper-dark); border-radius: 3px 8px 8px 3px; overflow: hidden; }
  .notebook .band { position: absolute; left: 154px; top: 0; width: 6px; height: 100%; background: #0c0c0c; }
  .notebook .wordmark { position: absolute; left: 48px; top: 140px; color: var(--white); }
  .notebook .wordmark .name { font-size: 38px; }
  .notebook .wordmark .sub { font-size: 8px; }

  /* Business cards */
  .card { top: 746px; width: 203px; height: 112px; background: var(--paper-dark-2); color: var(--white); }
  .card-front { left: 190px; }
  .card-back { left: 414px; }
  .card-front .wordmark { position: absolute; left: 21px; top: 17px; }
  .card-front .wordmark .name { font-size: 17px; }
  .card-front .wordmark .sub { font-size: 3.6px; }
  .card-front .person { position: absolute; left: 36px; top: 57px; font-size: 6.5px; font-weight: 600; }
  .card-front .title { position: absolute; left: 126px; top: 58px; font-size: 4.6px; }
  .card-front .lines { position: absolute; left: 36px; top: 78px; font-size: 4.6px; line-height: 1.6; }
  .card-front .addr { position: absolute; left: 126px; top: 86px; font-size: 4.6px; line-height: 1.6; }
  .card-back .wordmark { position: absolute; left: 52px; top: 32px; }
  .card-back .wordmark .name { font-size: 34px; }
  .card-back .wordmark .sub { font-size: 7px; }

  /* Standalone logo */
  .logo-lockup { left: 1002px; top: 852px; color: var(--white); }
  .logo-lockup .name { font-size: 56px; }
  .logo-lockup .sub { font-size: 11.5px; }
</style>
</head>
<body>

  <div class="piece backing"></div>

  <article class="piece letterhead">
    <div class="wordmark"><span class="name">VELK</span><span class="sub">CONSULTING</span></div>
    <div class="recipient">
      <strong>MR. Daniel HARLOW</strong><br>
      <strong>Managing Director</strong><br>
      <span>12/08 Linden Court</span><br>
      <span>Oregon - 987654321</span>
    </div>
    <div class="date">Date : 01 July 2018</div>
    <div class="body-text">
      <p>Lorem ipsum dolor sit amet, justo platonem in per, dicant constituto ne eam. Aeque persecuti sit ea, at vis commodo tractatos vituperata, sea an albucius forensibus. Wisi quodsi id qui, duo tempor aliquam assentior eu, no diceret tibique definiebas mei. Id nec noster facilisi mandamus.</p>
      <p>Nullam definiebas signiferumque pro te, vel mutat lobortis conceptam in. Usu justo minimum an, ne regione sanctus praesent usu, eam ut adipisci volutpat. Vel odio tibique consequat ne, in dicit gubergren appellantur vis, quo ei omnis elitr. Qui ne enim dictas dissentiet, pro nulla quodsi deseruisse te. Vide prima eloquentiam pro ei, agam dicta in pro, eu persius propriae constituam sea. Ius ut iriure oblique laboramus, cu sed fugit commune invenire, viris repudiandae ex vis. Nullam definiebas signiferumque pro te, vel mutat lobortis conceptam in. Usu justo minimum an, ne regione sanctus praesent usu, eam ut adipisci volutpat. Vel odio tibique consequat ne, in dicit gubergren appellantur vis, quo ei omnis elitr. Qui ne enim dictas dissentiet, pro nulla quodsi deseruisse te. Vide prima eloquentiam pro ei, agam dicta in pro, eu persius propriae constituam sea. Ius ut iriure oblique laboramus, cu sed fugit commune invenire, viris repudiandae ex vis.</p>
    </div>
    <footer class="letter-footer">
      <span>112 N Elm Avenue, Fairview, OR 97024</span>
      <span class="sep"></span>
      <span><svg viewBox="0 0 10 10"><path d="M2 1l2 2-1 1.5c.8 1.4 1.6 2.2 3 3L7.5 6l2 2-1.5 1.5C4.5 9 1 5.5.5 2z" fill="var(--gold)"/></svg>000 000 0000</span>
      <span class="sep"></span>
      <span><svg viewBox="0 0 10 10"><rect x=".5" y="2" width="9" height="6.5" fill="none" stroke="var(--gold)"/><path d="M.5 2l4.5 3.5L9.5 2" fill="none" stroke="var(--gold)"/></svg>info@velkconsulting.com</span>
      <span class="sep"></span>
      <span><svg viewBox="0 0 10 10"><circle cx="5" cy="5" r="4.3" fill="none" stroke="var(--gold)"/><path d="M.7 5h8.6M5 .7c-2.5 2.8-2.5 5.8 0 8.6M5 .7c2.5 2.8 2.5 5.8 0 8.6" fill="none" stroke="var(--gold)" stroke-width=".7"/></svg>www.velkconsulting.com</span>
    </footer>
  </article>

  <section class="piece envelope-back">
    <svg class="flap" width="386" height="203" viewBox="0 0 386 203" aria-hidden="true">
      <path d="M0 0 L178 108 Q193 116 208 108 L386 0" fill="#121212" stroke="#0b0b0b" stroke-width="1"/>
    </svg>
    <div class="wordmark"><span class="name">VELK</span><span class="sub">CONSULTING</span></div>
  </section>

  <section class="piece envelope-front">
    <div class="wordmark"><span class="name">VELK</span><span class="sub">CONSULTING</span></div>
    <div class="contact">&#9743; 000 000 000<br>&#9673; www.velkconsulting.com</div>
    <div class="return"><strong>VELK Consulting</strong><br>112 N Elm Avenue, Fairview, OR 97024</div>
  </section>

  <section class="piece notebook">
    <div class="wordmark"><span class="name">VELK</span><span class="sub">CONSULTING</span></div>
    <div class="band"></div>
  </section>

  <section class="piece card card-front">
    <div class="wordmark"><span class="name">VELK</span><span class="sub">CONSULTING</span></div>
    <div class="person">Daniel HARLOW</div>
    <div class="title">Managing Director</div>
    <div class="lines">&#9743; 000 000 000<br>&#9993; daniel@velkconsulting.com<br>&#9673; www.velkconsulting.com</div>
    <div class="addr">112 N Elm Avenue<br>Fairview, OR 97024</div>
  </section>

  <section class="piece card card-back">
    <div class="wordmark"><span class="name">VELK</span><span class="sub">CONSULTING</span></div>
  </section>

  <div class="piece logo-lockup wordmark"><span class="name">VELK</span><span class="sub">CONSULTING</span></div>

</body>
</html>
```